Velvet Riot Rising Line of Sparkling Wine & Spirits

Back info: Nora Beth Quill Owner 555-318-4402 1480 E. Harlow Ave, Bldg. 2, & 3, Lodi Ca. 95871
Sparkling Wines & Memorabilia www.velvetriotrising.com
Ok I have uploaded the winning design. The color that I am after is the Fushia, Raspberry, Red, Matte Satin Matalic Finish. With a 24 Karet Gold color Foil. The Bottle is on the top row and it's the 2nd Bottle in. That is the Color that I want. This is the style of font. Make sure that you put what we're advertising. Good Luck to you all. Warmest regards, Nora
21 & up UniSex
Sparkling Wine and Memorabilia
there listed up above.....

```html
<!DOCTYPE html>
<html lang="en">
<head>
<meta charset="utf-8">
<title>Velvet Riot Rising — Business Card</title>
<link rel="stylesheet" href="https://fonts.googleapis.com/css2?family=Pinyon+Script&family=Poppins:wght@400;600&display=swap">
<style>
  :root {
    --stage: #2c2c2e;
    --raspberry-hot: #ec0c8c;
    --raspberry-mid: #c10c6a;
    --raspberry-deep: #860a3f;
    --gold: #e2b52c;
    --gold-soft: #d9a825;
    --charcoal: #2a2a2a;
  }
  * { margin: 0; padding: 0; box-sizing: border-box; }
  html, body {
    width: 1200px; height: 689px; overflow: hidden;
    background: var(--stage);
  }
  .canvas {
    width: 1200px; height: 689px;
    display: flex; align-items: center; justify-content: center; gap: 48px;
  }
  .card {
    position: relative;
    width: 540px; height: 310px;
    border-radius: 22px;
    overflow: hidden;
    background:
      radial-gradient(ellipse 70% 55% at 40% 30%, var(--raspberry-hot) 0%, transparent 70%),
      radial-gradient(ellipse 60% 60% at 75% 80%, var(--raspberry-deep) 0%, transparent 75%),
      linear-gradient(160deg, var(--raspberry-mid) 0%, var(--raspberry-deep) 100%);
    font-family: "Poppins", sans-serif;
    color: var(--gold);
  }
  /* Front */
  .card--front {
    display: flex; flex-direction: column; align-items: center; justify-content: center;
    gap: 22px;
  }
  .brand-name {
    font-family: "Poppins", sans-serif;
    font-weight: 600;
    font-size: 38px;
    color: var(--charcoal);
    letter-spacing: 0.5px;
  }
  .tagline {
    font-size: 15px;
    font-weight: 400;
    letter-spacing: 1.5px;
    text-transform: uppercase;
    color: var(--gold);
  }
  /* Back */
  .brand-mark {
    position: absolute; top: 34px; right: 34px;
    display: flex; align-items: center; gap: 10px;
    font-weight: 600; font-size: 17px; color: var(--gold);
  }
  .brand-mark__dot {
    width: 12px; height: 12px; background: var(--gold);
  }
  .accent-bar {
    position: absolute; left: 0; top: 96px;
    width: 16px; height: 34px; background: var(--gold-soft);
  }
  .holder { position: absolute; left: 40px; top: 82px; }
  .holder__name {
    font-family: "Pinyon Script", cursive;
    font-size: 36px; line-height: 1; color: var(--gold);
  }
  .holder__role { font-size: 15px; margin-top: 4px; }
  .address {
    position: absolute; left: 40px; top: 172px;
    font-size: 14px; line-height: 1.35;
  }
  .contacts {
    position: absolute; left: 40px; bottom: 26px;
    list-style: none; font-size: 14px; line-height: 1.5;
  }
  .contacts li { display: flex; align-items: center; gap: 9px; }
  .contacts svg { width: 14px; height: 14px; flex: none; }
</style>
</head>
<body>
<main class="canvas">
  <section class="card card--front" aria-label="Card front">
    <h1 class="brand-name">Velvet Riot Rising</h1>
    <p class="tagline">Sparkling Wines &amp; Memorabilia</p>
  </section>

  <section class="card card--back" aria-label="Card back">
    <div class="brand-mark"><span class="brand-mark__dot"></span>Velvet Riot Rising</div>
    <span class="accent-bar"></span>
    <div class="holder">
      <p class="holder__name">Nora Beth Quill</p>
      <p class="holder__role">Owner</p>
    </div>
    <p class="address">1480 E. Harlow Ave, Bldg. 2, &amp; 3,<br>Lodi Ca. 95871</p>
    <ul class="contacts">
      <li>
        <svg viewBox="0 0 24 24" fill="currentColor" aria-hidden="true"><path d="M6.6 10.8a15 15 0 0 0 6.6 6.6l2.2-2.2c.3-.3.7-.4 1-.2 1.1.4 2.3.6 3.6.6.6 0 1 .4 1 1V20c0 .6-.4 1-1 1A17 17 0 0 1 3 4c0-.6.4-1 1-1h3.5c.6 0 1 .4 1 1 0 1.3.2 2.5.6 3.6.1.3 0 .7-.2 1z"/></svg>
        555-318-4402
      </li>
      <li>
        <svg viewBox="0 0 24 24" fill="currentColor" aria-hidden="true"><path d="M2 5h20v14H2z M2 5l10 8 10-8" stroke="#860a3f" stroke-width="1.5"/></svg>
        hello@velvetriotrising.com
      </li>
      <li>
        <svg viewBox="0 0 24 24" fill="none" stroke="currentColor" stroke-width="2" aria-hidden="true"><circle cx="12" cy="12" r="9"/><path d="M3 12h18M12 3c3 3 3 15 0 18M12 3c-3 3-3 15 0 18"/></svg>
        www.velvetriotrising.com
      </li>
    </ul>
  </section>
</main>
</body>
</html>
```